New Flyer Design Project

PAGE 1

Change to 8th Annual Copperline Clash and the new date is January 24, 2026

12U, Middle School & High School - add Open 18+

Under Weigh-ins
Early Registration is $25.00
Deadline is January 18, 2026 at 11:59 PM

Regular Registration is $35.00
Deadline is January 21, 2026 at 11:59 PM

Late / On-site Registration is $50.00
Deadline is January 23, 2026 at 5:00 PM
Change 500 to 750

Under Weigh-Ins - Change
January 24, 2025 to January 23, 2026
January 25, 2025 to January 24, 2026

PAGE 2
Change 2024-2025 to 2025-2026

In the Division Line Fix the numbers 1, 2, 3, 4, 5, 6, 7, 8, 9, 10

Change 12/31/2024 to 12/31/2025 where it says "Age As Of"
Change to "Excluding the High School & Open Division"

```html
<!DOCTYPE html>
<html lang="en">
<head>
<meta charset="utf-8">
<title>8th Annual Copperline Clash</title>
<link href="https://fonts.googleapis.com/css2?family=Cinzel+Decorative:wght@900&family=Oswald:wght@400;500;600&display=swap" rel="stylesheet">
<style>
:root{
  --cream:#f7eedb;
  --ink:#1f1208;
  --maroon:#6b1b10;
  --maroon-deep:#5a150c;
  --brown:#7a4a2a;
  --brown-dark:#6a3e22;
  --beige:#d9c29a;
  --orange-a:#f65e3a;
  --orange-b:#f8a13c;
  --gold:#b38a12;
  --line:#ffffff;
}
*{margin:0;padding:0;box-sizing:border-box}
html,body{width:1200px;height:827px;overflow:hidden;background:#fff}
body{position:relative;font-family:"Oswald",sans-serif;font-variant:small-caps;color:var(--cream)}
.page{position:absolute;top:0;width:590px;height:827px;overflow:hidden;
  background:linear-gradient(180deg,#e7d4ae 0%,#cdb085 40%,#b8956a 100%)}
.page--left{left:0}
.page--right{left:610px}
.abs{position:absolute}

.event-title{position:absolute;text-align:center;font-family:"Cinzel Decorative",serif;font-weight:900;line-height:1;
  background:linear-gradient(180deg,#ffd36a 0%,#f29a1c 45%,#b4510a 100%);-webkit-background-clip:text;background-clip:text;color:transparent;
  filter:drop-shadow(2px 2px 0 #3a2412) drop-shadow(0 0 1px #3a2412)}
.event-title .line-top{display:block;font-size:25px;letter-spacing:-.5px}
.event-title .line-main{display:block;font-size:60px;margin-top:2px}

.org-pennant{left:477px;top:0;width:94px;height:122px;background:var(--gold);
  clip-path:polygon(0 0,100% 0,100% 100%,50% 82%,0 100%);display:flex;flex-direction:column;align-items:center;padding-top:22px;gap:8px}
.org-pennant .dot{width:40px;height:40px;border-radius:50%;background:#e9dcc0}
.org-pennant .name{font-size:15px;font-weight:600;color:var(--ink);font-variant:normal;letter-spacing:1px}

.event-date{left:0;width:470px;top:118px;text-align:center;color:var(--ink);font-size:18px;font-weight:500}
.event-venue{left:0;width:470px;top:137px;text-align:center;color:var(--ink);font-size:14.5px;font-weight:600}

.band{position:absolute;left:0;width:100%}
.band--schedule{top:175px;height:82px;background:var(--maroon)}
.band--registration{top:269px;height:246px;background:var(--brown)}
.band--weighins{top:538px;height:289px;background:var(--brown-dark)}

.pill{position:absolute;display:flex;align-items:center;justify-content:center;border-radius:6px;
  background:linear-gradient(90deg,var(--orange-a),var(--orange-b));color:var(--cream);font-weight:500}
.pill--mats{left:149px;top:161px;width:87px;height:28px;font-size:21px}
.pill--fee{left:30px;width:231px;height:23px;font-size:15px}
.pill--weighins{left:122px;top:524px;width:139px;height:29px;font-size:22px}

.text-line{position:absolute;left:29px;white-space:nowrap;font-weight:500}
.schedule{font-size:15px}
.deadline{font-size:15.5px}
.notice{font-size:15px}
.small{font-size:9.6px;font-weight:400}
.admission{font-size:12px}

.art{position:absolute}
.art--warrior-left{left:330px;top:178px;width:260px;height:649px;
  background:radial-gradient(ellipse at 55% 30%,#8e6a4a 0%,#6b4a30 45%,rgba(90,60,38,.2) 80%,rgba(90,60,38,0) 100%);
  border-radius:45% 45% 0 0}

/* right page */
.table-panel{left:18px;top:126px;width:547px;height:309px;border-radius:18px;background:var(--maroon-deep)}
.weights{position:absolute;left:28px;top:139px;width:529px}
.weights .caption{height:19px;background:linear-gradient(90deg,var(--orange-a),var(--orange-b));border:1.5px solid var(--line);
  text-align:center;font-size:14px;font-weight:500;line-height:16px}
.weights .cols{display:flex;align-items:flex-start}
.col{display:flex;flex-direction:column;border-right:1px solid var(--line)}
.col:first-child{border-left:1px solid var(--line)}
.col .div-no{height:11px;background:var(--orange-a);font-size:9px;line-height:11px;text-align:center;border-bottom:1px solid var(--line)}
.col .head{height:47px;display:flex;align-items:center;justify-content:center;text-align:center;font-size:9.5px;line-height:10px;border-bottom:1px solid var(--line);padding:0 1px}
.col .w{height:11.2px;font-size:9.5px;line-height:11px;text-align:center;border-bottom:1px solid var(--line);font-weight:500}
.col--empty .w{height:11.2px}

.art--mats{left:0;top:468px;width:590px;height:177px;
  background:linear-gradient(90deg,#5a4a3a 0%,#3f4c4e 20%,#8b3a36 45%,#354246 70%,#c9503b 90%,#5a4a3a 100%)}
.band--awards{top:645px;height:182px;background:var(--brown)}
.art--warrior-right{left:0;top:588px;width:135px;height:239px;border-radius:45% 45% 0 0;
  background:linear-gradient(180deg,#7e5c40 0%,#5c3d26 100%)}
.art--singlets{left:430px;top:650px;width:150px;height:170px;border-radius:10px;
  background:linear-gradient(90deg,#6d1c1c 0%,#8a2a28 45%,#cdb89a 55%,#b7a282 100%)}
.awards-text{left:150px;width:258px;top:672px;text-align:center;font-size:24.5px;font-weight:600;line-height:27.5px;color:var(--cream)}
</style>
</head>
<body>

<section class="page page--left">
  <h1 class="event-title" style="left:40px;width:420px;top:10px"><span class="line-top">8th Annual Copperline</span><span class="line-main">Clash</span></h1>
  <div class="abs org-pennant"><span class="dot"></span><span class="name">CRWA</span></div>
  <p class="abs event-date">Saturday, January 24, 2026</p>
  <p class="abs event-venue">Harborview Event Hall 418 Marsh Landing Rd Pinewood, NC</p>

  <div class="band band--schedule"></div>
  <div class="band band--registration"></div>
  <div class="band band--weighins"></div>

  <div class="art art--warrior-left" role="img" aria-label="Illustration of a Greek warrior in a crested helmet, armour and red cloak holding a shield"></div>

  <div class="pill pill--mats">6 Mats</div>
  <p class="text-line schedule" style="top:192px">K-5, 6U, 8U, 10U - [Wrestling Starts at 8:30AM]</p>
  <p class="text-line schedule" style="top:212px">12U, Middle Schol &amp; High School, Open 18+ [Wrestling Starts at 1:30PM]</p>
  <p class="text-line schedule" style="top:231px">Register @www.grapplereg.com</p>

  <div class="pill pill--fee" style="top:284px">Early Registration is $25.00</div>
  <p class="text-line deadline" style="top:307px">Deadline is January 18, 2026 at 11:59 PM</p>
  <div class="pill pill--fee" style="top:334px">Regular Registration is $35.00</div>
  <p class="text-line deadline" style="top:359px">Deadline is January 21, 2026 at 11:59 PM</p>
  <div class="pill pill--fee" style="top:387px">Late / On-site Registration is $50.00</div>
  <p class="text-line deadline" style="top:411px">Deadline is January 23, 2026 at 5:00 PM</p>
  <p class="text-line notice" style="top:444px">Registeration is limited to the first 750 Wrestlers</p>
  <p class="text-line notice" style="top:462px">Non-CRWA Card Holders will pay an additional $5.00</p>
  <p class="text-line notice" style="top:481px">at weigh-ins.</p>

  <div class="pill pill--weighins">Weigh-Ins</div>
  <p class="text-line small" style="top:557px">January 23, 2026 - 5:00PM to 7:00PM [Early Weigh-in -$10 cash due at scale]</p>
  <p class="text-line small" style="top:572px">January 24, 2026 - 6:00AM to 7:30AM [K-5, 6U, 8U, 10U]</p>
  <p class="text-line small" style="top:587px">January 24, 2026 - 11:00AM to 12:00PM [12 &amp; Under, Middle School, High School, Open 18+]</p>
  <p class="text-line small" style="top:617px">Tenths are waived/dropped at weigh-ins, Satelite weigh-ins will not be allowed.</p>
  <p class="text-line small" style="top:632px">high School Division are given 2lbs, growth allowance</p>
  <p class="text-line small" style="top:648px">Custom medals will be given to the top 3 individual finishers in each bracket</p>
  <p class="text-line small" style="top:678px">Custom Awards will be awarded to the top 4 teams,</p>
  <p class="text-line small" style="top:693px">Referee decisions will be final,</p>
  <p class="text-line small" style="top:709px">Copper Creek Athletics is not responsible for accidents, injuries, or theft during</p>
  <p class="text-line small" style="top:724px">the tournament.</p>
  <p class="text-line admission" style="top:744px">Admission : $10 per person</p>
  <p class="text-line small" style="top:769px">For more information, contact Tournament Director Dale Whitford: (555)014-2287</p>
  <p class="text-line small" style="top:784px">Hotels Available On-Site</p>
  <p class="text-line small" style="top:799px">Riverside Lodge: (555)013-5000 / Oakmont Suites: (555)013-7400 / Pinecrest Inn: (555)013-8300</p>
</section>

<section class="page page--right">
  <h1 class="event-title" style="left:90px;width:410px;top:10px"><span class="line-top">8th Annual Copperline</span><span class="line-main">Clash</span></h1>

  <div class="abs table-panel"></div>
  <div class="weights">
    <div class="caption">2025-2026 CRWA Age &amp; Weight Clases</div>
    <div class="cols">
      <div class="col col--empty" style="width:51px"><div class="div-no">Division</div><div class="head">Age As Of 12/31/2025</div><div class="w"></div><div class="w"></div><div class="w"></div><div class="w"></div><div class="w"></div><div class="w"></div></div>
      <div class="col" style="width:46px"><div class="div-no">1</div><div class="head">6 &amp; Under</div><div class="w">36</div><div class="w">40</div><div class="w">44</div><div class="w">48</div><div class="w">52</div><div class="w">56</div><div class="w">60</div><div class="w">HWT</div></div>
      <div class="col" style="width:50px"><div class="div-no">2</div><div class="head">8 &amp; Under</div><div class="w">40</div><div class="w">44</div><div class="w">48</div><div class="w">52</div><div class="w">56</div><div class="w">60</div><div class="w">64</div><div class="w">68</div><div class="w">72</div><div class="w">76</div><div class="w">80</div><div class="w">84</div><div class="w">88</div><div class="w">92</div><div class="w">HWT</div></div>
      <div class="col" style="width:51px"><div class="div-no">3</div><div class="head">10 &amp; Under</div><div class="w">52</div><div class="w">56</div><div class="w">60</div><div class="w">64</div><div class="w">68</div><div class="w">72</div><div class="w">76</div><div class="w">80</div><div class="w">84</div><div class="w">88</div><div class="w">92</div><div class="w">96</div><div class="w">100</div><div class="w">110</div><div class="w">HWT</div></div>
      <div class="col" style="width:55px"><div class="div-no">4</div><div class="head">12 &amp; Under</div><div class="w">68</div><div class="w">72</div><div class="w">76</div><div class="w">83</div><div class="w">90</div><div class="w">98</div><div class="w">106</div><div class="w">113</div><div class="w">120</div><div class="w">126</div><div class="w">132</div><div class="w">138</div><div class="w">144</div><div class="w">150</div><div class="w">157</div><div class="w">165</div><div class="w">175</div><div class="w">190</div><div class="w">HWT</div></div>
      <div class="col" style="width:30px"><div class="div-no">5</div><div class="head">Middle School</div><div class="w">76</div><div class="w">83</div><div class="w">90</div><div class="w">98</div><div class="w">106</div><div class="w">113</div><div class="w">120</div><div class="w">126</div><div class="w">132</div><div class="w">138</div><div class="w">144</div><div class="w">150</div><div class="w">157</div><div class="w">165</div><div class="w">175</div><div class="w">190</div><div class="w">215</div><div class="w">HWT</div></div>
      <div class="col" style="width:52px"><div class="div-no">6</div><div class="head">Girls K-5</div><div class="w">40</div><div class="w">44</div><div class="w">48</div><div class="w">52</div><div class="w">56</div><div class="w">60</div><div class="w">64</div><div class="w">68</div><div class="w">72</div><div class="w">76</div><div class="w">80</div><div class="w">84</div><div class="w">88</div><div class="w">92</div><div class="w">96</div><div class="w">100</div><div class="w">110</div><div class="w">120</div><div class="w">HWT</div></div>
      <div class="col" style="width:48px"><div class="div-no">7</div><div class="head">Girls 6th - 8th</div><div class="w">76</div><div class="w">83</div><div class="w">90</div><div class="w">98</div><div class="w">106</div><div class="w">113</div><div class="w">120</div><div class="w">126</div><div class="w">132</div><div class="w">138</div><div class="w">144</div><div class="w">150</div><div class="w">157</div><div class="w">165</div><div class="w">175</div><div class="w">190</div><div class="w">215</div><div class="w">HWT</div></div>
      <div class="col" style="width:46px"><div class="div-no">8</div><div class="head">Women's Grades 9 - 12</div><div class="w">100</div><div class="w">107</div><div class="w">114</div><div class="w">120</div><div class="w">126</div><div class="w">132</div><div class="w">145</div><div class="w">152</div><div class="w">165</div><div class="w">185</div><div class="w">HWT</div></div>
      <div class="col" style="width:51px"><div class="div-no">9</div><div class="head">Men's Under Grades 9 - 12</div><div class="w">106</div><div class="w">113</div><div class="w">120</div><div class="w">126</div><div class="w">132</div><div class="w">138</div><div class="w">144</div><div class="w">150</div><div class="w">157</div><div class="w">165</div><div class="w">175</div><div class="w">190</div><div class="w">215</div><div class="w">HWT</div></div>
      <div class="col" style="width:49px"><div class="div-no">10</div><div class="head">Open 18+</div><div class="w">125</div><div class="w">133</div><div class="w">141</div><div class="w">149</div><div class="w">157</div><div class="w">165</div><div class="w">174</div><div class="w">184</div><div class="w">197</div><div class="w">215</div><div class="w">HWT</div></div>
    </div>
  </div>

  <div class="art art--mats" role="img" aria-label="Aerial photo of six wrestling mats in red and black laid out in an arena"></div>
  <div class="band band--awards"></div>
  <div class="art art--warrior-right" role="img" aria-label="Illustration of a Greek warrior in a crested helmet holding a spear"></div>
  <div class="art art--singlets" role="img" aria-label="Two custom tournament singlets in maroon and tan with warrior artwork"></div>
  <p class="abs awards-text">Custom singlets are awarded to champions in all weights Excluding the High School &amp; Open Division</p>
</section>

</body>
</html>
```